Point of sale box designs , I have templets.

I need point of sale box design according to my requirements.
I have all files at the ready. Each windows file has a;; the information you will need.
see files I uploded.
This project is 90% cut and paste. look into all the windows files for instructions ,text, bar codes and there placement.
You only have to draw the 3 steps on how to use the product.
Industry/Entity Type
General consumer product.
Nice to have
- Taxi cab yellow background with black text.

```html
<!DOCTYPE html>
<html lang="en">
<head>
<meta charset="utf-8">
<title>Saucy Sachet Snipper – Blister Card</title>
<link rel="stylesheet" href="https://fonts.googleapis.com/css2?family=Arimo:wght@400;700&display=swap">
<style>
  :root {
    --backdrop: #e5e5e5;
    --cab-yellow: #ffcc00;
    --ink: #111111;
    --label-white: #ffffff;
    --pill-black: #000000;
  }
  * { margin: 0; padding: 0; box-sizing: border-box; }
  html, body {
    width: 1200px; height: 1200px; overflow: hidden;
    background: var(--backdrop);
    font-family: "Arimo", Arial, sans-serif;
    color: var(--ink);
  }
  .stage { position: relative; width: 1200px; height: 1200px; }

  .card {
    position: absolute; top: 202px;
    width: 342px; height: 795px;
    background: var(--cab-yellow);
    border-radius: 12px 12px 0 0;
  }
  .card--back { left: 233px; }
  .card--front { left: 625px; }

  .hang-slot {
    position: absolute; height: 36px;
    background: var(--label-white);
    border-radius: 8px;
  }
  .hang-slot::before {
    content: ""; position: absolute;
    width: 22px; height: 22px; border-radius: 50%;
    background: var(--label-white);
    top: -10px; left: var(--notch-x);
    transform: translateX(-50%);
  }
  .card--back .hang-slot { left: 32px; top: 32px; width: 265px; --notch-x: 126px; }
  .card--front .hang-slot { left: 35px; top: 22px; width: 264px; --notch-x: 126px; }

  .label-box { position: absolute; background: var(--label-white); border-radius: 4px; }

  .heading {
    position: absolute; left: 34px; top: 106px;
    font-size: 22px; font-weight: 400; letter-spacing: 0.2px; white-space: nowrap;
  }
  .region {
    position: absolute; font-weight: 700; white-space: nowrap;
    transform: translate(-50%, -50%);
  }
  .card--back .region { font-size: 19px; }
  .card--front .region { font-size: 14px; }

  .pill {
    position: absolute; background: var(--pill-black);
    border-radius: 999px; color: var(--label-white);
    transform: translateY(-50%);
  }
  .pill__hole {
    position: absolute; top: 50%; transform: translate(-50%, -50%);
    background: var(--label-white); border-radius: 50%;
  }
  .pill__name {
    position: absolute; top: 50%; transform: translate(-50%, -50%);
    text-align: center; font-weight: 700; line-height: 1.15; white-space: nowrap;
  }
  .card--back .pill { left: 184px; width: 148px; height: 50px; }
  .card--back .pill__hole { left: 19px; width: 16px; height: 28px; }
  .card--back .pill__name { left: 85px; font-size: 11px; }
  .card--front .pill { left: 166px; width: 166px; height: 55px; }
  .card--front .pill__hole { left: 21px; width: 17px; height: 32px; }
  .card--front .pill__name { left: 95px; font-size: 12.5px; }

  .back-info {
    position: absolute; left: 170px; top: 680px;
    transform: translateX(-50%);
    text-align: center; font-weight: 700; font-size: 17px;
    line-height: 24.6px; white-space: nowrap;
  }

  .pitch {
    position: absolute; left: 21px; top: 225px;
    font-size: 24px; line-height: 36.2px; white-space: nowrap;
  }
  .fine-print {
    position: absolute; top: 757px; font-size: 16px; white-space: nowrap;
  }
  .fine-print--origin { left: 27px; }
  .fine-print--care { right: 26px; top: 758px; }
</style>
</head>
<body>
<main class="stage">

  <section class="card card--back" aria-label="Card back">
    <div class="hang-slot"></div>
    <h2 class="heading">INVENTORY BAR CODES</h2>

    <div class="label-box" style="left:18px; top:171px; width:135px; height:166px;"></div>
    <div class="region" style="left:87px; top:377px;">US &amp; CANADA</div>

    <div class="label-box" style="left:18px; top:422px; width:135px; height:167px;"></div>
    <div class="region" style="left:86px; top:632px;">EU</div>

    <div class="pill" style="top:202px;"><span class="pill__hole"></span><span class="pill__name">Saucy<br>Sachet Snipper</span></div>
    <div class="pill" style="top:325px;"><span class="pill__hole"></span><span class="pill__name">Saucy<br>Sachet Snipper</span></div>
    <div class="pill" style="top:443px;"><span class="pill__hole"></span><span class="pill__name">Saucy<br>Sachet Snipper</span></div>
    <div class="pill" style="top:566px;"><span class="pill__hole"></span><span class="pill__name">Saucy<br>Sachet Snipper</span></div>

    <p class="back-info">Visit us at<br>WWW.PACKETPOKESHOP.COM<br>Copyright &amp; Tredmarked<br>Not a this empty from smal children</p>
  </section>

  <section class="card card--front" aria-label="Card front">
    <div class="hang-slot"></div>

    <div class="label-box" style="left:29px; top:70px; width:78px; height:97px;"></div>
    <div class="region" style="left:69px; top:184px;">US &amp; CANADA</div>
    <div class="label-box" style="left:235px; top:72px; width:78px; height:97px;"></div>
    <div class="region" style="left:273px; top:185px;">EU</div>

    <p class="pitch">So simple to<br>use even a<br>child can do it<br>don’t pur<br>the packet<br>between<br>your teeth<br>to open it<br>That’s just<br>gross.use our<br>Saucy<br>sachet<br>snipper.</p>

    <div class="pill" style="top:250px;"><span class="pill__hole"></span><span class="pill__name">Saucy<br>Sachet Snipper</span></div>
    <div class="pill" style="top:389px;"><span class="pill__hole"></span><span class="pill__name">Saucy<br>Sachet Snipper</span></div>
    <div class="pill" style="top:522px;"><span class="pill__hole"></span><span class="pill__name">Saucy<br>Sachet Snipper</span></div>
    <div class="pill" style="top:660px;"><span class="pill__hole"></span><span class="pill__name">Saucy<br>Sachet Snipper</span></div>

    <p class="fine-print fine-print--origin">Made in China</p>
    <p class="fine-print fine-print--care">Dishwater safe</p>
  </section>

</main>
</body>
</html>
```